Harborline Auto LLC

Car Dealer Customer Service
Address: 2874 Cresthaven Road, Shelbyville, TN 37162
web: www.harborlineautoxq.net
email: harborlineautoxq@mailnest.example
Phone: (931) 555-0148
Phone: (629) 555-0173

```html
<!DOCTYPE html>
<html lang="en">
<head>
<meta charset="utf-8">
<title>Harborline Auto LLC – Business Card</title>
<link href="https://fonts.googleapis.com/css2?family=Archivo+Black&family=Arimo:wght@400;700&display=swap" rel="stylesheet">
<style>
  :root {
    --blue: #1d78a8;
    --gold: #eab347;
    --white: #ffffff;
    --backdrop: #2a2a2a;
  }
  * { margin: 0; padding: 0; box-sizing: border-box; }
  html, body {
    width: 1200px; height: 1015px; overflow: hidden;
    background: var(--backdrop);
  }
  .sheet {
    width: 1200px; height: 1015px;
    display: flex; flex-direction: column; align-items: center; justify-content: center;
    gap: 36px;
  }
  .card {
    position: relative;
    width: 780px; height: 446px;
    overflow: hidden;
    box-shadow: 0 12px 30px rgba(0,0,0,.5);
  }
  .heading { font-family: "Archivo Black", "Arial Black", sans-serif; }
  .body-text { font-family: "Arimo", Arial, sans-serif; }

  /* front */
  .card-front { background: var(--blue); }
  .card-front .brand {
    position: absolute; left: 0; right: 0; top: 110px;
    display: flex; flex-direction: column; align-items: center; gap: 22px;
  }
  .brand-dot {
    width: 96px; height: 96px; border-radius: 50%;
    background: var(--white);
  }
  .card-front .brand-name {
    color: var(--white); font-size: 40px; letter-spacing: 2px; text-transform: uppercase;
  }
  .card-front .tagline-band {
    position: absolute; left: 0; right: 0; top: 340px; height: 44px;
    background: var(--gold);
    display: flex; align-items: center; justify-content: center;
    color: var(--white); font-size: 20px; letter-spacing: 3px; text-transform: uppercase;
  }

  /* back */
  .card-back { background: var(--white); }
  .card-back .info-panel {
    position: absolute; left: 340px; top: 0; right: 0; bottom: 0;
    background: var(--blue);
  }
  .card-back .brand {
    position: absolute; left: 0; width: 340px; top: 80px;
    display: flex; flex-direction: column; align-items: center; gap: 20px;
  }
  .card-back .brand-dot { background: var(--blue); width: 110px; height: 110px; }
  .card-back .brand-name {
    color: var(--blue); font-size: 27px; letter-spacing: 1px; text-transform: uppercase;
  }
  .card-back .web-band {
    position: absolute; left: 0; right: 0; top: 300px; height: 44px;
    background: var(--gold);
    display: flex; align-items: center; padding-left: 120px;
    color: var(--white); font-size: 17px;
  }
  .contact {
    position: absolute; left: 380px; top: 46px; color: var(--white);
  }
  .contact .person { font-size: 24px; text-transform: uppercase; line-height: 1; }
  .contact .role { font-size: 16px; margin-top: 4px; }
  .contact .address { font-size: 16px; margin-top: 20px; line-height: 1.3; }
  .contact .lines { list-style: none; margin-top: 22px; font-size: 16px; }
  .contact .lines li { display: flex; align-items: center; gap: 8px; line-height: 1.45; }
  .contact .lines svg { width: 16px; height: 16px; flex: none; }
</style>
</head>
<body>
<main class="sheet">
  <section class="card card-front">
    <div class="brand">
      <span class="brand-dot"></span>
      <span class="brand-name heading">Harborline Auto</span>
    </div>
    <div class="tagline-band heading">Car Dealer Customer Service</div>
  </section>

  <section class="card card-back">
    <div class="info-panel"></div>
    <div class="web-band body-text">www.harborlineautoxq.net</div>
    <div class="brand">
      <span class="brand-dot"></span>
      <span class="brand-name heading">Harborline Auto</span>
    </div>
    <div class="contact body-text">
      <p class="person heading">Marcus Delaney</p>
      <p class="role">Managing Director</p>
      <p class="address">2874 Cresthaven Road<br>Shelbyville, TN 37162</p>
      <ul class="lines">
        <li><svg viewBox="0 0 24 24" fill="none" stroke="#fff" stroke-width="2"><path d="M5 3h4l2 5-3 2a12 12 0 0 0 6 6l2-3 5 2v4a2 2 0 0 1-2 2A17 17 0 0 1 3 5a2 2 0 0 1 2-2z"/></svg>(931) 555-0148</li>
        <li><svg viewBox="0 0 24 24" fill="none" stroke="#fff" stroke-width="2"><path d="M5 3h4l2 5-3 2a12 12 0 0 0 6 6l2-3 5 2v4a2 2 0 0 1-2 2A17 17 0 0 1 3 5a2 2 0 0 1 2-2z"/></svg>(629) 555-0173</li>
        <li><svg viewBox="0 0 24 24" fill="#fff"><path d="M2 5h20v14H2z"/><path d="M2 5l10 8 10-8" fill="none" stroke="#1d78a8" stroke-width="2"/></svg>harborlineautoxq@mailnest.example</li>
      </ul>
    </div>
  </section>
</main>
</body>
</html>
```